LEARN Business Skills so you can Earn a good living

size of the poster is 8”x 10.75" plus 0.25" bleed.
Please leave 1 inch on the bottoum for footer
I want a design a poster that will attract people's attention.
I appreciate a creative ad however the ad should not take away from being able to clearly read the text.
-I also appreciate a simple creative ad that is not too busy.
-you can use graphics, vectors, or pictures of real people.
-however, if you use real people it should be a white male that is wearing a white shirt and look like a professional person.

Target Market(s)

Potential young business people

Industry/Entity Type

education

Requirements
Must have
• easy to read the text
Nice to have
• I would like a "creative" simple ad that is easy to be read
Should not have
• pictures of women

```html
<!DOCTYPE html>
<html lang="en">
<head>
<meta charset="utf-8">
<title>Skill Up Earn – Business Enrichment Course</title>
<link rel="stylesheet" href="https://fonts.googleapis.com/css2?family=League+Spartan:wght@500;600;700&family=Poppins:wght@400;500;600&display=swap">
<style>
  :root {
    --blue: #42ade6;
    --ink: #4b4b4d;
    --body: #555558;
    --paper: #ffffff;
    --footer: #49494b;
    --footer-text: #ececec;
    --tick: #a9d8f3;
    --photo-light: #f4f4f4;
    --photo-dark: #e4e4e6;
  }
  * { box-sizing: border-box; margin: 0; padding: 0; }
  html, body { width: 723px; height: 1200px; overflow: hidden; background: var(--paper); }
  .poster { position: relative; width: 723px; height: 1200px; background: var(--paper); overflow: hidden; font-family: "Poppins", sans-serif; color: var(--body); }

  .hero-photo {
    position: absolute; left: 462px; top: 64px; width: 261px; height: 866px;
    background: linear-gradient(160deg, var(--photo-light) 0%, var(--photo-dark) 100%);
  }

  .headline { position: absolute; left: 0; top: 0; width: 470px; height: 500px; }
  .headline text { font-family: "League Spartan", sans-serif; }

  .tagline {
    position: absolute; left: 52px; top: 512px; width: 290px;
    font-size: 21px; font-weight: 500; line-height: 27px; color: var(--body);
  }

  .skills-banner {
    position: absolute; left: 52px; top: 634px; width: 301px; height: 85px;
    background: var(--blue); border-radius: 8px 0 0 8px;
    box-shadow: 0 4px 6px rgba(0,0,0,0.12);
    padding: 20px 0 0 27px;
    font-size: 20px; font-weight: 600; line-height: 26px; color: #fff;
  }
  .skills-banner strong { color: var(--ink); font-weight: 600; }

  .benefits { position: absolute; left: 30px; top: 745px; width: 330px; height: 140px; display: flex; }
  .benefit { flex: 1; text-align: center; position: relative; }
  .benefit + .benefit::before {
    content: ""; position: absolute; left: 0; top: 0; width: 2px; height: 140px;
    background: linear-gradient(to bottom, #e4e4e4, #f4f4f4);
  }
  .benefit svg { display: block; margin: 4px auto 6px; }
  .benefit p { font-size: 17px; font-weight: 500; line-height: 22px; color: var(--body); }

  .topics {
    position: absolute; left: 0; top: 930px; width: 723px; height: 270px;
    background: var(--footer);
  }
  .topic-columns { position: absolute; top: 38px; left: 0; width: 100%; }
  .topic-list { position: absolute; list-style: none; }
  .topic-list li {
    position: relative; padding-left: 16px;
    font-size: 11px; line-height: 20px; color: var(--footer-text); text-transform: uppercase; white-space: nowrap;
  }
  .topic-list li.two-line { line-height: 13px; padding-top: 4px; padding-bottom: 3px; }
  .topic-list li::before {
    content: ""; position: absolute; left: 0; top: 6px; width: 9px; height: 9px;
    border: 1.5px solid var(--tick); border-radius: 1px;
  }
  .topic-list li::after {
    content: ""; position: absolute; left: 3px; top: 6px; width: 4px; height: 6px;
    border: solid var(--tick); border-width: 0 2px 2px 0; transform: rotate(40deg);
  }
  .col-1 { left: 52px; } .col-2 { left: 250px; } .col-3 { left: 410px; } .col-4 { left: 585px; }

  .web-address {
    position: absolute; left: 0; top: 198px; width: 100%; text-align: center;
    font-size: 22px; letter-spacing: 1px; color: #fff; font-weight: 400;
  }
  .web-address span { color: var(--blue); font-weight: 500; }
</style>
</head>
<body>
<div class="poster">

  <div class="hero-photo" role="img" aria-label="Smiling young professional man in a white shirt pointing toward the headline"></div>

  <svg class="headline" viewBox="0 0 470 500" aria-label="Skill Up Earn – Business Enrichment Course">
    <text x="52" y="157" font-size="118" font-weight="700" fill="var(--blue)" textLength="397" lengthAdjust="spacingAndGlyphs">SKILL UP</text>
    <text x="52" y="313" font-size="190" font-weight="700" fill="var(--blue)" textLength="397" lengthAdjust="spacingAndGlyphs">EARN</text>
    <text x="52" y="386" font-size="30" font-weight="500" fill="var(--ink)" textLength="213" lengthAdjust="spacing">BUSINESS</text>
    <text x="52" y="423" font-size="40" font-weight="700" fill="var(--blue)" textLength="213" lengthAdjust="spacingAndGlyphs">ENRICHMENT</text>
    <text x="52" y="480" font-size="66" font-weight="600" fill="var(--ink)" textLength="211" lengthAdjust="spacingAndGlyphs">COURSE</text>
    <rect x="52" y="489" width="38" height="4" rx="2" fill="var(--blue)"/>
  </svg>

  <p class="tagline">A proven success of helping people in their livelihoods</p>

  <div class="skills-banner">Business skills that will<br><strong>help you:</strong></div>

  <div class="benefits">
    <div class="benefit">
      <svg width="48" height="44" viewBox="0 0 48 44" aria-hidden="true">
        <circle cx="17" cy="9" r="8" fill="var(--ink)"/>
        <path d="M3 40 C3 26 9 21 17 21 C23 21 27 23 29 27 L29 40 Z" fill="var(--ink)"/>
        <rect x="27" y="27" width="19" height="14" rx="2" fill="var(--blue)"/>
        <rect x="32" y="23" width="9" height="5" rx="1" fill="none" stroke="var(--blue)" stroke-width="2"/>
        <line x1="27" y1="33" x2="46" y2="33" stroke="#fff" stroke-width="1.5"/>
      </svg>
      <p>Get a<br>quality<br>job</p>
    </div>
    <div class="benefit">
      <svg width="48" height="44" viewBox="0 0 48 44" aria-hidden="true">
        <rect x="4" y="28" width="6" height="14" fill="var(--ink)"/>
        <rect x="13" y="22" width="6" height="20" fill="var(--ink)"/>
        <rect x="22" y="26" width="6" height="16" fill="var(--ink)"/>
        <rect x="31" y="18" width="6" height="24" fill="var(--ink)"/>
        <polyline points="4,20 14,11 23,17 40,4" fill="none" stroke="var(--blue)" stroke-width="3"/>
        <polygon points="44,1 42,11 34,4" fill="var(--blue)"/>
      </svg>
      <p>Start/grow<br>your<br>business</p>
    </div>
    <div class="benefit">
      <svg width="48" height="44" viewBox="0 0 48 44" aria-hidden="true">
        <rect x="10" y="2" width="28" height="26" fill="var(--blue)"/>
        <text x="24" y="22" font-family="Poppins, sans-serif" font-size="18" font-weight="600" fill="#fff" text-anchor="middle">$</text>
        <path d="M4 20 L24 33 L44 20 L44 42 L4 42 Z" fill="var(--ink)"/>
      </svg>
      <p>Increase<br>your<br>salary</p>
    </div>
  </div>

  <section class="topics">
    <div class="topic-columns">
      <ul class="topic-list col-1">
        <li>Business Admiistration</li>
        <li>Small Business Management</li>
        <li>Finance</li>
        <li>Investments</li>
        <li>Computers</li>
      </ul>
      <ul class="topic-list col-2">
        <li>Accounting</li>
        <li>Sales&nbsp; Marketing</li>
        <li class="two-line">Project Management<br>Interviewing Skills</li>
        <li>Business Law</li>
        <li>Negotiation</li>
      </ul>
      <ul class="topic-list col-3">
        <li>Public Speaking</li>
        <li>Import/Export</li>
        <li>Information Technoloy</li>
        <li>Distribution</li>
        <li>Marketing</li>
      </ul>
      <ul class="topic-list col-4">
        <li>Bookkeeping</li>
        <li>Real Estate</li>
        <li>Health Care</li>
        <li>Management</li>
        <li>E-Commerce</li>
      </ul>
    </div>
    <p class="web-address">www.<span>skillupearn</span>.com</p>
  </section>

</div>
</body>
</html>
```